Need website for Dating "Game" App

I need a one or two page website for a new dating "game" app (patent pending) called wooSpark.net. The game will be "interactive" and is designed to be a fun, safe and nonthreatening way to help two people get to know more about each other "before making a face to face date". The App will be configured somewhat like a dating app/website where members browse profiles to find someone they are interested in getting to know.
I am looking for a design that will capture the attention of singles who are tired of wasting time on face to face dates with individuals they are not compatible with. This website will be used as somewhat of a launch page for a Fundlaunch campaign because the app is still in the development stage.

Target Market(s)

Single daters who are looking for a compatible mate

Industry/Entity Type

Dating

Number of Pages Required

2 page

Requirements
Must have
• Mention that the game is Patent Pending
• Must be whimsical but with a classy-clean look (the game is designed to be fun)
• I have a 30 second video completed that I would like incorporated on the website.
• Logo colors must stay the same
• Page must direct to my upcoming Fundlaunch campaign - (Dating App is still in development stage)
Nice to have
• 1. The game will populate relationship/lifestyle like questions to two players who opt to play the game together. The design could possibly have some fun relationship questions "raining" down on the page.
• 2. Tag line...MEET - PLAY - DATE (T.M.)
• Meet - Browse profiles to find someone whom you want to get to know better and invite them to play!
• Play - Many dating sites take you through a grueling set of questions before you upload a profile. You are then matched with individuals that an "algorithm" determines you are most compatible with. The problem with this method is that only the algorithm knows what areas you and those individuals have in common. WooSpark.net alleviates the guesswork by placing the power of the algorithm in your hands with a fun, safe and nonthreatening game that helps you get to know your person of interest before meeting face to face!
• Date -
• 3. "Wouldn't it be great to get to know someone better before making a date?"
Should not have
• Nothing raunchy.
• I don't want the basic 'dating website' look (although I do like the "Tulip Finds Lantern" site.

```html
<!DOCTYPE html>
<html lang="en">
<head>
<meta charset="utf-8">
<title>wooSpark.net — Meet, Play, Date</title>
<link href="https://fonts.googleapis.com/css2?family=Lato:wght@400;700;900&display=swap" rel="stylesheet">
<style>
:root{
  --red:#d4121a;
  --red-deep:#b10d12;
  --ink:#1a1a1a;
  --text:#333;
  --white:#fff;
  --dark:#1d1d1d;
  --line:#e9c4c6;
}
*{box-sizing:border-box;margin:0;padding:0}
html,body{width:1200px;height:2908px;overflow:hidden}
body{font-family:'Lato',Arial,sans-serif;color:var(--text);background:var(--white);position:relative}
.abs{position:absolute}

/* hero */
.hero{left:0;top:0;width:1200px;height:665px;overflow:hidden;background:#2a1c16}
.hero-photo{position:absolute;inset:0;background:
  radial-gradient(ellipse 260px 330px at 330px 330px,rgba(150,110,85,.55),transparent 70%),
  radial-gradient(ellipse 240px 300px at 900px 360px,rgba(120,80,65,.5),transparent 70%),
  radial-gradient(ellipse 200px 120px at 960px 620px,rgba(190,30,45,.75),transparent 75%),
  radial-gradient(ellipse 160px 200px at 590px 300px,rgba(110,40,30,.55),transparent 75%),
  linear-gradient(90deg,#3a2a20 0%,#5a4536 35%,#4d3a2e 60%,#3b2a22 100%)}
.hero-shade{position:absolute;left:0;top:380px;width:1200px;height:285px;background:linear-gradient(180deg,transparent,rgba(10,6,4,.45))}
.topbar{position:absolute;left:0;top:0;width:1200px;height:100px;background:rgba(255,255,255,.92)}
.brand{position:absolute;left:130px;top:40px;display:flex;align-items:center;gap:10px}
.brand-dot{width:30px;height:30px;border-radius:50%;background:var(--red)}
.brand-name{font-size:24px;font-weight:900;color:var(--red-deep);line-height:1}
.brand-tag{position:absolute;left:152px;top:74px;font-size:10px;color:var(--ink);font-weight:700}
.login{position:absolute;left:775px;top:18px}
.field{display:flex;align-items:center;width:210px;height:24px;margin-bottom:3px;background:#f1f1f1}
.field i{display:flex;align-items:center;justify-content:center;width:24px;height:24px;background:var(--red)}
.field span{font-size:10px;color:#555;padding-left:8px}
.login-btn{position:absolute;left:210px;top:0;width:83px;height:51px;background:var(--red);color:var(--white);font-size:14px;font-weight:700;display:flex;align-items:center;justify-content:center}
.login-link{font-size:10px;color:var(--red);margin-top:2px}
.arrow{position:absolute;top:345px}
.headline{position:absolute;left:0;top:430px;width:1200px;text-align:center;color:var(--white);font-size:35px;font-weight:900;letter-spacing:.3px;text-shadow:0 2px 6px rgba(0,0,0,.5)}
.stores{position:absolute;left:382px;top:505px;display:flex;gap:9px}
.store{width:215px;height:76px;background:#000;border:2px solid #aaa;border-radius:10px;color:var(--white);display:flex;flex-direction:column;justify-content:center;padding-left:30px}
.store small{font-size:11px}
.store b{font-size:25px;font-weight:400;line-height:1.1}

/* intro */
.intro{left:135px;top:713px;width:930px;text-align:center;font-size:13.5px;line-height:24px;color:var(--ink)}

/* video */
.video{left:0;top:840px;width:1200px;height:368px;background:
  radial-gradient(ellipse 300px 90px at 560px 250px,rgba(250,190,90,.7),transparent 70%),
  linear-gradient(180deg,#4a3020 0%,#8a5a2e 35%,#c47a22 58%,#2a1a10 80%,#111 100%)}
.play{position:absolute;left:563px;top:148px}

/* features */
.phone{left:135px;top:1262px;width:270px;height:533px;border-radius:36px;background:linear-gradient(160deg,#f7f7f7,#d8d8d8);border:3px solid #bbb}
.phone-speaker{position:absolute;left:105px;top:30px;width:55px;height:6px;border-radius:3px;background:#999}
.phone-home{position:absolute;left:100px;top:486px;width:66px;height:22px;border-radius:11px;border:2px solid #aaa}
.phone-screen{position:absolute;left:14px;top:62px;width:236px;height:410px;background:#fff;overflow:hidden}
.app-bar{height:46px;border-bottom:2px solid var(--red);display:flex;align-items:center;justify-content:center;gap:5px}
.app-bar i{width:10px;height:10px;border-radius:50%;background:var(--red)}
.app-bar span{font-size:11px;font-weight:900;color:var(--red-deep)}
.app-thumbs{position:absolute;left:14px;top:62px;width:80px}
.app-thumbs div{width:80px;height:70px;margin-bottom:21px;border:2px solid var(--red);background:linear-gradient(180deg,#d9c6b6,#6f5a4c)}
.app-feature{position:absolute;left:108px;top:56px;width:118px;height:346px;background:linear-gradient(180deg,#fafafa 0%,#e6ddd5 40%,#cfc3b8 100%)}
.feat-title{left:500px;top:1320px;font-size:24px;font-weight:700;color:var(--ink)}
.feat-title em{font-style:normal;color:var(--red)}
.feat-rule{left:480px;top:1366px;width:590px;height:2px;background:linear-gradient(90deg,var(--red),#f3c0c2)}
.feat-mark{left:466px;top:1358px;width:18px;height:18px;border-radius:50%;background:var(--red)}
.feat-list{left:500px;top:1392px;width:560px;list-style:none}
.feat-list li{position:relative;padding-left:28px;height:89px}
.feat-list li svg{position:absolute;left:0;top:2px}
.feat-list h3{font-size:15.5px;font-weight:700;color:var(--ink);margin-bottom:6px}
.feat-list p{font-size:12px;line-height:18px;color:#444}

/* steps */
.steps{left:0;top:1862px;width:1200px;height:416px;background:radial-gradient(ellipse at 40% 50%,#c8141b,#a30c11 70%,#8f0a0e)}
.step{position:absolute;top:0;width:260px;text-align:center;color:var(--white)}
.step-icon{width:200px;height:200px;margin:45px auto 0;border-radius:50%;background:var(--white);display:flex;align-items:center;justify-content:center}
.step h2{font-size:25px;font-weight:700;margin-top:40px;letter-spacing:.5px}
.step p{font-size:19px;font-weight:700;line-height:26px;margin-top:4px}

/* about */
.about-photo{left:720px;top:2278px;width:480px;height:442px;background:
  radial-gradient(ellipse 140px 200px at 380px 160px,rgba(120,80,55,.6),transparent 70%),
  linear-gradient(90deg,#fff 0%,#eee6de 30%,#c9a788 65%,#8a5e40 100%)}
.about-list{left:130px;top:2360px;width:600px;list-style:none}
.about-list li{position:relative;padding-left:38px;font-size:16px;line-height:26px;color:var(--ink);margin-bottom:14px}
.about-list li::before{content:"";position:absolute;left:4px;top:7px;width:13px;height:13px;border-radius:50%;background:var(--red)}

/* contact */
.contact{left:0;top:2720px;width:1200px;height:146px;background:var(--dark);text-align:center;color:var(--white)}
.contact h2{font-size:29px;font-weight:400;margin-top:14px}
.contact h2 em{font-style:normal;color:var(--red)}
.contact p{font-size:13px;margin-top:12px}
.social{display:flex;justify-content:center;gap:8px;margin-top:14px}
.social span{width:26px;height:26px;border-radius:50%;background:#2f7fd6;border:2px solid var(--white)}
.social span.alt{background:var(--red)}
.footer{left:0;top:2866px;width:1200px;height:42px;background:var(--red);color:var(--white);font-size:12px;display:flex;align-items:center;justify-content:space-between;padding:0 135px}
.footer b{font-weight:700}
</style>
</head>
<body>

<section class="abs hero">
  <div class="hero-photo" role="img" aria-label="Photo of a smiling couple toasting with red wine at a restaurant table"></div>
  <div class="hero-shade"></div>
  <header class="topbar">
    <div class="brand"><span class="brand-dot"></span><span class="brand-name">wooSpark.net</span></div>
    <div class="brand-tag">don't do dating without it</div>
    <form class="login">
      <div class="field"><i><svg width="12" height="12" viewBox="0 0 12 12"><circle cx="6" cy="4" r="2.5" fill="#fff"/><path d="M1 12a5 5 0 0 1 10 0z" fill="#fff"/></svg></i><span>User Name</span></div>
      <div class="field"><i><svg width="12" height="12" viewBox="0 0 12 12"><rect x="2" y="5" width="8" height="7" fill="#fff"/><path d="M4 5V3a2 2 0 0 1 4 0v2" fill="none" stroke="#fff" stroke-width="1.4"/></svg></i><span>Password</span></div>
      <div class="login-link">Have Account? Login Here</div>
      <div class="login-btn">LOG IN</div>
    </form>
  </header>
  <svg class="arrow" style="left:28px" width="30" height="50" viewBox="0 0 30 50"><polyline points="26,2 4,25 26,48" fill="none" stroke="#d4121a" stroke-width="3"/></svg>
  <svg class="arrow" style="left:1142px" width="30" height="50" viewBox="0 0 30 50"><polyline points="4,2 26,25 4,48" fill="none" stroke="#ddd" stroke-width="3"/></svg>
  <h1 class="headline">YOU'RE NEVER ALONE WITH A DATING</h1>
  <div class="stores">
    <div class="store"><small>GET IT ON</small><b>Droid Shelf</b></div>
    <div class="store"><small>Download on the</small><b>Pocket Market</b></div>
  </div>
</section>

<p class="abs intro">Many dating sites take you through a grueling set of questions before you upload a profile. wooSpark.net is a Patent Pending dating game that puts the power of the algorithm in your hands, so two people can get to know each other before a face to face date. The app is in development now, so back our upcoming Fundlaunch campaign and be among the first to play. Meet, play, then date with confidence.</p>

<section class="abs video" role="img" aria-label="Video still: silhouette of a couple on a bench at sunset">
  <svg class="play" width="74" height="74" viewBox="0 0 74 74"><circle cx="37" cy="37" r="34" fill="none" stroke="#d4121a" stroke-width="5"/><polygon points="29,22 53,37 29,52" fill="#d4121a"/></svg>
</section>

<div class="abs phone">
  <div class="phone-speaker"></div>
  <div class="phone-screen">
    <div class="app-bar"><i></i><span>wooSpark.net</span></div>
    <div class="app-thumbs" role="img" aria-label="Member profile photos"><div></div><div></div><div></div><div></div></div>
    <div class="app-feature" role="img" aria-label="Featured member photo"></div>
  </div>
  <div class="phone-home"></div>
</div>
<h2 class="abs feat-title">Lorem Ipsum Dolor Sit Amet, <em>Consectetuer Adipisc</em></h2>
<div class="abs feat-rule"></div>
<div class="abs feat-mark"></div>
<ul class="abs feat-list">
  <li><svg width="16" height="16" viewBox="0 0 16 16"><rect x="1" y="2" width="12" height="12" fill="none" stroke="#222" stroke-width="1.5"/><polyline points="3,8 7,12 15,1" fill="none" stroke="#222" stroke-width="2"/></svg><h3>Lorem Ipsum Dolor Sit Amet, Consectetuer Adipiscing Elit, Sed Diam</h3><p>Ut wisi enim ad minim veniam, quis nostrud exerci tation ullamcorper suscipit lobortis nisl ut aliquip ex ea commodo consequat.</p></li>
  <li><svg width="16" height="16" viewBox="0 0 16 16"><rect x="1" y="2" width="12" height="12" fill="none" stroke="#222" stroke-width="1.5"/><polyline points="3,8 7,12 15,1" fill="none" stroke="#222" stroke-width="2"/></svg><h3>Lorem Ipsum Dolor Sit Amet, Consectetuer Adipiscing Elit, Sed Diam</h3><p>Ut wisi enim ad minim veniam, quis nostrud exerci tation ullamcorper suscipit lobortis nisl ut aliquip ex ea commodo consequat.</p></li>
  <li><svg width="16" height="16" viewBox="0 0 16 16"><rect x="1" y="2" width="12" height="12" fill="none" stroke="#222" stroke-width="1.5"/><polyline points="3,8 7,12 15,1" fill="none" stroke="#222" stroke-width="2"/></svg><h3>Lorem Ipsum Dolor Sit Amet, Consectetuer Adipiscing Elit, Sed Diam</h3><p>Ut wisi enim ad minim veniam, quis nostrud exerci tation ullamcorper suscipit lobortis nisl ut aliquip ex ea commodo consequat.</p></li>
  <li><svg width="16" height="16" viewBox="0 0 16 16"><rect x="1" y="2" width="12" height="12" fill="none" stroke="#222" stroke-width="1.5"/><polyline points="3,8 7,12 15,1" fill="none" stroke="#222" stroke-width="2"/></svg><h3>Lorem Ipsum Dolor Sit Amet, Consectetuer Adipiscing Elit, Sed Diam</h3><p>Ut wisi enim ad minim veniam, quis nostrud exerci tation ullamcorper suscipit lobortis nisl ut aliquip ex ea commodo consequat.</p></li>
</ul>

<section class="abs steps">
  <svg class="abs" style="left:0;top:0" width="1200" height="416" viewBox="0 0 1200 416">
    <path d="M300 185 Q390 210 470 180" fill="none" stroke="#fff" stroke-width="2"/>
    <polyline points="458,172 472,180 460,190" fill="none" stroke="#fff" stroke-width="2"/>
    <path d="M705 75 Q790 20 880 55" fill="none" stroke="#fff" stroke-width="2"/>
    <polyline points="866,46 880,55 867,64" fill="none" stroke="#fff" stroke-width="2"/>
  </svg>
  <div class="step" style="left:135px"><div class="step-icon"><svg width="84" height="84" viewBox="0 0 84 84" aria-label="Meet icon"><circle cx="28" cy="28" r="12" fill="#b10d12"/><path d="M6 72a22 22 0 0 1 44 0z" fill="#b10d12"/><circle cx="56" cy="28" r="12" fill="#d4121a"/><path d="M34 72a22 22 0 0 1 44 0z" fill="#d4121a"/></svg></div><h2>MEET</h2><p>Browse<br>Profiles Paly</p></div>
  <div class="step" style="left:470px"><div class="step-icon"><svg width="90" height="80" viewBox="0 0 90 80" aria-label="Play icon"><path d="M6 8h50a6 6 0 0 1 6 6v26a6 6 0 0 1-6 6H24l-12 10V46H6a6 6 0 0 1-6-6V14a6 6 0 0 1 6-6z" fill="#b10d12"/><path d="M40 30h44a6 6 0 0 1 6 6v24a6 6 0 0 1-6 6h-4v10l-12-10H40a6 6 0 0 1-6-6V36a6 6 0 0 1 6-6z" fill="#d4121a"/><text x="31" y="36" font-family="Lato,sans-serif" font-size="24" font-weight="900" fill="#fff" text-anchor="middle">?</text><text x="62" y="57" font-family="Lato,sans-serif" font-size="24" font-weight="900" fill="#fff" text-anchor="middle">?</text></svg></div><h2>PLAY</h2><p>Play With Your<br>Compatible Person</p></div>
  <div class="step" style="left:808px"><div class="step-icon"><svg width="78" height="78" viewBox="0 0 78 78" aria-label="Date icon"><rect x="4" y="12" width="70" height="62" rx="6" fill="#d4121a"/><rect x="4" y="12" width="70" height="16" rx="6" fill="#b10d12"/><rect x="18" y="4" width="6" height="16" rx="3" fill="#b10d12"/><rect x="54" y="4" width="6" height="16" rx="3" fill="#b10d12"/><polyline points="24,50 35,61 56,38" fill="none" stroke="#fff" stroke-width="6" stroke-linecap="round" stroke-linejoin="round"/></svg></div><h2>DATE</h2><p>Make<br>A Date</p></div>
</section>

<div class="abs about-photo" role="img" aria-label="Photo of a woman holding a phone with the app open"></div>
<ul class="abs about-list">
  <li>Many dating sites take you through a gruelling set of questions before you upload a profile.</li>
  <li>You are then matched with individuals that an “algorithm” determines you are most compatible with.</li>
  <li>The problem with this method is that only the algorithm knows what areas you and those individuals have in common.</li>
  <li>We alleviates the guesswork by placing the power of the algorithm in your hands with a fun, safe and nonthreatening game that helps you get to know your person of interest before face to face meeting!</li>
</ul>

<section class="abs contact">
  <h2>Contact <em>Us</em></h2>
  <p>Questions for us? Technical issues, suggestions, or other inquiries? Contact us!</p>
  <div class="social"><span></span><span></span><span></span><span class="alt"></span></div>
</section>

<footer class="abs footer"><span>Copyright 2016 wooSpark.net &nbsp;| &nbsp;All Rights Reserved</span><b>Privacy &amp; Terms</b></footer>

</body>
</html>
```